Small Business Consulting Firm Needs Letterhead

We need a letterhead for our company "Brightpath Plus". Our company does outbound calling and mailing to business owner's companies who have taken high interest loans. These loans tend to put these businesses in a big financial bind short term, and we help them find better financial options. We would like the design to match our colors of our logo. Headers and footers would look nice, but we are open. We would want it to include our address, website, phone, and email info. Our address - 2000 E. Lamar Blvd. Suite 600Website - www.safeguardtoday.comEmail - info@safeguardtoday.comPhone - 855-726-1938
Industry/Entity Type
Financial Planning
Look and feel
Each slider illustrates characteristics of the customer's brand and the style your logo design should communicate.

```html
<!DOCTYPE html>
<html lang="en">
<head>
<meta charset="utf-8">
<title>Brightpath Plus Letterhead</title>
<link rel="stylesheet" href="https://fonts.googleapis.com/css2?family=Arimo:wght@400;700&family=Montserrat:wght@400&display=swap">
<style>
  :root {
    --brand-blue: #0a7cc4;
    --brand-green: #64a338;
    --ink: #222222;
    --wordmark: #3d3d3f;
    --paper: #ffffff;
    --sig-fill: #ececec;
  }
  * { margin: 0; padding: 0; box-sizing: border-box; }
  html, body { width: 918px; height: 1200px; overflow: hidden; background: var(--paper); }
  .letterhead {
    position: relative;
    width: 918px;
    height: 1200px;
    background: var(--paper);
    font-family: "Arimo", Arial, sans-serif;
    color: var(--ink);
  }
  .top-rule-blue { position: absolute; left: 0; top: 0; width: 100%; height: 8px; background: var(--brand-blue); }
  .top-rule-green { position: absolute; left: 0; top: 8px; width: 100%; height: 2px; background: var(--brand-green); }

  .brand-mark {
    position: absolute; left: 164px; top: 48px;
    width: 82px; height: 82px; background: var(--brand-green);
  }
  .brand-name {
    position: absolute; left: 60px; top: 154px; width: 298px;
    text-align: center;
    font-family: "Montserrat", Arial, sans-serif;
    font-weight: 400; font-size: 27px; letter-spacing: 2.5px;
    color: var(--wordmark); text-transform: uppercase; white-space: nowrap;
  }

  .contact {
    position: absolute; right: 75px; top: 76px;
    text-align: right; font-size: 16px; line-height: 30.5px;
  }
  .contact .label { color: var(--brand-blue); font-weight: 700; }

  .letter-body {
    position: absolute; left: 134px; top: 339px; width: 650px;
    font-size: 18px; line-height: 23.6px;
  }
  .salutation { margin-bottom: 38px; }
  .letter-body p.para { margin-bottom: 20px; }
  .letter-body p.justified { text-align: justify; }
  .closing { position: absolute; left: 134px; top: 898px; font-size: 18px; }
  .signature {
    position: absolute; left: 134px; top: 928px; width: 86px; height: 62px;
    background: var(--sig-fill); border-radius: 6px;
  }

  .footer-band {
    position: absolute; left: 0; top: 1136px; width: 100%; height: 30px;
    background: var(--brand-green);
  }
  .footer-stripes { position: absolute; left: 410px; top: 0; }
  .footer-url {
    position: absolute; right: 52px; top: 3px;
    color: var(--paper); font-size: 18px; letter-spacing: 3.2px;
  }
</style>
</head>
<body>
<div class="letterhead">
  <div class="top-rule-blue"></div>
  <div class="top-rule-green"></div>

  <div class="brand-mark"></div>
  <div class="brand-name">Brightpath Plus</div>

  <div class="contact">
    <div><span class="label">Phone - </span>855-726-1938</div>
    <div><span class="label">Email - </span>info@brightpathplus.com</div>
    <div><span class="label">Website - </span>www.brightpathplus.com</div>
    <div>4170 W. Corwin Ave. Suite 310</div>
  </div>

  <div class="letter-body">
    <p class="salutation">Dear :</p>
    <p class="para">Lorem ipsum dolor sit amet, consectetur adipiscing elit. Aenean ut ipsum eget massa hendrerit vestibulum vel in velit. Donec pretium neque nec elit.</p>
    <p class="para">Aliquam porta lectus nec mauris ornare venenatis. Vivamus nec est turpis, et cursus sem. Mauris vehicula erat in diam auctor at bibendum nibh lacinia.</p>
    <p class="para justified">Morbi imperdiet neque vehicula nunc convallis gravida. Vestibulum iaculis pretium placerat. Integer consequat, est sit amet facilisis eleifend, nibh nibh varius orci, eget dapibus arcu dui non purus. Pellentesque in magna mauris. Duis enim sapien, dictum vitae condimentum a, pulvinar vel lacus. Mauris et molestie nibh. Vestibulum vitae nulla at metus elementum porta sit amet interdum elit. Nulla sollicitudin neque eu nulla volutpat congue.</p>
    <p class="para justified">Etiam pellentesque, velit id dapibus fermentum, turpis sapien ornare dui, tincidunt ligula odio congue purus. Nunc sed ante dui, in porta lectus. Cras nec sem lorem. In hac habitasse platea dictumst. Maecenas id diam quis dui porta tristique. Sed id egestas felis. Donec ullamcorper mattis posuere. Phasellus fermentum eleifend tortor vel dapibus. Vestibulum ante ipsum.</p>
  </div>

  <p class="closing">Sincerely,</p>
  <div class="signature" role="img" aria-label="Handwritten signature of the sender"></div>

  <div class="footer-band">
    <svg class="footer-stripes" width="120" height="30" viewBox="0 0 120 30">
      <polygon points="0,0 8,0 30,30 22,30" fill="#ffffff"/>
      <polygon points="8,0 20,0 42,30 30,30" fill="var(--brand-blue)"/>
      <polygon points="20,0 23,0 45,30 42,30" fill="#ffffff"/>
      <polygon points="23,0 35,0 57,30 45,30" fill="var(--brand-blue)"/>
      <polygon points="35,0 43,0 65,30 57,30" fill="#ffffff"/>
    </svg>
    <div class="footer-url">www.brightpathplus.com</div>
  </div>
</div>
</body>
</html>
```